Corinnehabbard.com

1. Conceptualization and designing of the site Homepage. The Homepage design will be completely customized and based on your design instructions (i.e. preferred colors, links to reference sites that you want us to take reference from if any etc) and the recently completed logo design.
2. Upon homepage design approval, based on it we will be creating the layout for the other 4 site inner pages (i.e. About page, Contact page, Services page, and Insights (publications, media).
3. Once all the inner page designs are approved, we will get the designs built (will make sure that the site is completely Responsive - works on all devices) within your provided WIX account.
4. We will add the static text and images provided by you to the Home page, About page, Contact page, and the Services page. For the 2 Insights sub-pages, we will add 1-2 sample Publications and Media entries.
once you confirm the total number of required entries for the 2 sub-pages, I will accordingly quote you on the same
5. Integration of a Contact form on the Contact page that will email the filled in details to your mail id.

```html
<!DOCTYPE html>
<html lang="en">
<head>
<meta charset="utf-8">
<title>Corinne Habbard Consulting</title>
<link href="https://fonts.googleapis.com/css2?family=Poppins:wght@400;500;600;700&display=swap" rel="stylesheet">
<style>
:root{
  --blue:#0b94dc;
  --blue-dark:#0a5f8f;
  --orange:#f39200;
  --green:#17882f;
  --red:#e2202a;
  --ink:#1f1f1f;
  --muted:#666;
  --light:#f4f4f4;
  --line:#d9d9d9;
  --footer:#2b2b2b;
  --white:#fff;
}
*{box-sizing:border-box;margin:0;padding:0}
html,body{width:1200px;height:4188px;overflow:hidden}
body{font-family:'Poppins',sans-serif;color:var(--ink);background:var(--white);position:relative}
.abs{position:absolute}
.btn{display:inline-block;background:var(--orange);color:var(--white);font-size:16px;padding:8px 30px;border-radius:4px}
.rule{width:120px;height:3px;background:var(--red)}
.fill{position:absolute}

/* header */
.site-header{top:0;left:0;width:1200px;height:88px;background:var(--white)}
.brand{left:110px;top:22px;display:flex;align-items:center;gap:12px}
.brand-dot{width:40px;height:40px;border-radius:50%;background:var(--blue)}
.brand-name{font-size:17px;font-weight:600;color:var(--blue-dark);line-height:1.1;text-transform:uppercase}
.main-nav{left:450px;top:30px;display:flex;gap:30px;font-size:16px}
.call-box{left:912px;top:0;width:288px;height:88px;background:var(--orange);color:var(--white);padding:14px 30px}
.call-box b{font-size:22px;display:block}
.call-box span{font-size:16px}

/* hero */
.hero-panel{top:88px;left:0;width:472px;height:552px;background:var(--blue);color:var(--white);padding:100px 0 0 110px}
.hero-panel h4{font-size:28px;font-weight:600;margin-bottom:14px}
.hero-panel h1{font-size:40px;font-weight:600;line-height:1.2;text-transform:uppercase;margin-bottom:18px}
.hero-panel .rule{margin-bottom:20px}
.hero-panel p{font-size:16px;line-height:1.45;width:330px;margin-bottom:36px}
.hero-photo{top:88px;left:472px;width:728px;height:552px;background:linear-gradient(135deg,#c9ccce,#6a737b 60%,#2d3540)}

/* offer */
.offer{top:640px;left:0;width:1200px;height:600px;background:var(--light)}
.offer h2{position:absolute;top:80px;width:100%;text-align:center;color:var(--green);font-size:38px;font-weight:600}
.offer .rule{position:absolute;top:138px;left:540px}
.offer-grid{top:188px;left:100px;width:1000px;height:372px}
.offer-cell{position:absolute;width:333px;height:166px;text-align:center;padding-top:52px;color:var(--blue);font-size:16px;font-weight:500}
.offer-cell svg{display:block;margin:0 auto 14px}
.offer-cell.feature{background:var(--blue);color:var(--white);top:-20px;height:186px;padding:20px 30px 0}
.offer-cell.feature h3{font-size:17px;font-weight:600;margin-bottom:12px}
.offer-cell.feature p{font-size:14px;line-height:1.4;margin-bottom:14px}
.offer-cell.feature .btn{font-size:14px;padding:6px 24px}
.vline{position:absolute;width:1px;background:var(--line)}
.hline{position:absolute;height:1px;background:var(--line)}

/* about */
.about-frame{top:1480px;left:396px;width:200px;height:345px;border:16px solid #ececec}
.about-photo{top:1332px;left:108px;width:424px;height:428px;background:linear-gradient(160deg,#c7b9ad,#5c4a40 60%,#1e1c1d)}
.about-copy{top:1400px;left:652px;width:440px}
.about-copy h2{color:var(--green);font-size:40px;font-weight:600;margin-bottom:8px}
.about-copy .rule{margin-bottom:26px}
.about-copy p{font-size:15px;line-height:1.5;color:var(--muted);margin-bottom:8px}
.about-copy p.link{color:var(--blue);margin-bottom:22px}

/* training */
.training-panel{top:1908px;left:0;width:600px;height:664px;background:var(--blue);color:var(--white)}
.training-panel h2{position:absolute;top:78px;left:212px;font-size:36px;font-weight:600;line-height:1.4;text-transform:uppercase}
.training-panel .title-bar{position:absolute;top:106px;left:112px;width:80px;height:3px;background:var(--white)}
.t-card{position:absolute;left:112px;width:468px;height:100px;background:var(--blue-dark);border:2px solid #58b8ec;display:flex;align-items:center;padding:0 20px;gap:22px}
.t-card svg{flex:none}
.t-card h3{font-size:16px;font-weight:600;margin-bottom:4px}
.t-card p{font-size:13px;line-height:1.4}
.training-photo{top:1908px;left:600px;width:600px;height:432px;background:linear-gradient(120deg,#9fa9b0,#3f4e5d 55%,#1a2430)}
.play{position:absolute;left:260px;top:176px}
.training-note{top:2340px;left:600px;width:600px;height:232px;background:var(--light);padding:52px 0 0 52px}
.training-note h3{color:var(--green);font-size:40px;font-weight:600;margin-bottom:12px}
.training-note .rule{margin-bottom:14px}
.training-note p{font-size:15px;line-height:1.5;color:var(--muted);width:440px}

/* insights */
.insights h2{position:absolute;top:2644px;width:1200px;text-align:center;color:var(--green);font-size:38px;font-weight:600}
.insights .rule{position:absolute;top:2702px;left:540px}
.post{position:absolute;top:2760px;width:304px}
.post-img{height:252px}
.post h3{font-size:20px;font-weight:500;line-height:1.35;margin:36px 0 10px}
.post a{font-size:14px;color:var(--orange);text-decoration:underline}
.view-more{top:3172px;left:536px;font-size:16px}

/* contact */
.map{top:3288px;left:0;width:540px;height:584px;background:linear-gradient(160deg,#eef0e8,#dfe6d6)}
.map svg{position:absolute;left:282px;top:176px}
.contact{top:3288px;left:540px;width:660px;height:584px;background:var(--light)}
.contact h2{position:absolute;top:64px;left:100px;color:var(--green);font-size:40px;font-weight:600;text-transform:uppercase}
.contact .dash{position:absolute;top:90px;left:60px;width:30px;height:3px;background:var(--red)}
.field{position:absolute;left:60px;width:490px;border-bottom:1px solid #9a9a9a;font-size:16px;padding-bottom:12px}
.contact .btn{position:absolute;left:60px;top:456px;font-size:15px;padding:6px 30px}

/* footer */
.site-footer{top:3872px;left:0;width:1200px;height:316px;background:var(--footer);color:var(--white)}
.foot-brand{position:absolute;top:40px;width:1200px;text-align:center}
.foot-brand .brand-dot{margin:0 auto 10px;background:var(--white)}
.foot-brand span{font-size:18px;font-weight:600;text-transform:uppercase;line-height:1.2;display:block}
.foot-nav{position:absolute;top:210px;width:1200px;display:flex;justify-content:center;gap:56px;font-size:20px}
.foot-line{position:absolute;top:256px;left:0;width:1200px;height:1px;background:#555}
.foot-legal{position:absolute;top:276px;left:200px;width:820px;display:flex;gap:40px;font-size:14px}
.foot-legal .links{margin-left:auto;display:flex;gap:30px}
.foot-legal .links span{text-decoration:underline}
</style>
</head>
<body>

<header class="site-header abs">
  <div class="brand abs"><div class="brand-dot"></div><div class="brand-name">Corinne Habbard<br><small style="font-size:11px">Consulting</small></div></div>
  <nav class="main-nav abs"><span>Home</span><span>About us</span><span>Insights</span><span>Services</span><span>Contact us</span></nav>
  <div class="call-box abs"><b>Call Us</b><span>+1 555 0100 2020</span></div>
</header>

<section class="hero-panel abs">
  <h4>WELCOME TO</h4>
  <h1>Corinne Habbard Consulting</h1>
  <div class="rule"></div>
  <p>Lorem ipsum dolor sit amet, consectetur adipiscing elit, sed do eiusmod tempor incididunt ut labore et dolore</p>
  <span class="btn">Get Started</span>
</section>
<div class="hero-photo abs" role="img" aria-label="Business team working together at a laptop in a bright office"></div>

<section class="offer abs">
  <h2>WHAT WE OFFFER</h2>
  <div class="rule"></div>
  <div class="offer-grid abs">
    <div class="vline" style="left:333px;top:0;height:372px"></div>
    <div class="vline" style="left:666px;top:0;height:372px"></div>
    <div class="hline" style="left:0;top:166px;width:1000px"></div>
    <div class="offer-cell" style="left:0;top:0">
      <svg width="56" height="48" viewBox="0 0 56 48" fill="none" stroke="#1f1f1f" stroke-width="2"><path d="M4 44h48M10 44V30h8v14M24 44V22h8v22M38 44V14h8v30M8 22l14-10 10 6 16-14"/><path d="M42 4h6v6" /></svg>
      Lorem ipsum dolor sit
    </div>
    <div class="offer-cell feature" style="left:333px">
      <h3>Lorem ipsum dolor sit</h3>
      <p>Lorem ipsum dolor sit amet, consectetur adipiscing elit, sed do eiusmod tempor</p>
      <span class="btn">Read More</span>
    </div>
    <div class="offer-cell" style="left:666px;top:0">
      <svg width="56" height="48" viewBox="0 0 56 48" fill="none" stroke="#1f1f1f" stroke-width="2"><circle cx="28" cy="18" r="12"/><circle cx="28" cy="15" r="4"/><path d="M21 25c2-4 12-4 14 0M14 44c2-6 8-8 14-8s12 2 14 8"/></svg>
      Lorem ipsum dolor sit
    </div>
    <div class="offer-cell" style="left:0;top:166px">
      <svg width="56" height="48" viewBox="0 0 56 48" fill="none" stroke="#1f1f1f" stroke-width="2"><circle cx="28" cy="16" r="12"/><path d="M28 10v12M22 16h12M12 44c2-8 8-12 16-12s14 4 16 12"/></svg>
      Lorem ipsum dolor sit
    </div>
    <div class="offer-cell" style="left:333px;top:166px">
      <svg width="56" height="48" viewBox="0 0 56 48" fill="none" stroke="#1f1f1f" stroke-width="2"><rect x="16" y="4" width="24" height="18"/><circle cx="12" cy="30" r="4"/><circle cx="28" cy="30" r="4"/><circle cx="44" cy="30" r="4"/><path d="M4 44c1-5 4-7 8-7s7 2 8 7M20 44c1-5 4-7 8-7s7 2 8 7M36 44c1-5 4-7 8-7s7 2 8 7"/></svg>
      Lorem ipsum dolor sit
    </div>
    <div class="offer-cell" style="left:666px;top:166px">
      <svg width="56" height="48" viewBox="0 0 56 48" fill="none" stroke="#1f1f1f" stroke-width="2"><circle cx="28" cy="24" r="8"/><circle cx="14" cy="12" r="6"/><circle cx="42" cy="12" r="6"/><circle cx="14" cy="38" r="6"/><circle cx="42" cy="38" r="6"/></svg>
      Lorem ipsum dolor sit
    </div>
  </div>
</section>

<div class="about-frame abs"></div>
<div class="about-photo abs" role="img" aria-label="Portrait of the consultant"></div>
<section class="about-copy abs">
  <h2>WHO WE ARE</h2>
  <div class="rule"></div>
  <p>Lorem ipsum dolor sit amet, consectetur adipiscing elit, sed do eiusmod tempor incididunt ut labore et dolore magna aliqua. Quis ipsum suspendisse ultrices gravida. Risus com modo viverra maecenas accumsan lacus vel facilisis.</p>
  <p class="link">Lorem ipsum dolor sit amet, consectetur adipiscing elit</p>
  <span class="btn">Read More</span>
</section>

<section class="training-panel abs">
  <div class="title-bar"></div>
  <h2>Training of<br>Registered Nurses</h2>
  <div class="t-card" style="top:204px">
    <svg width="48" height="40" viewBox="0 0 48 40" fill="none" stroke="#f39200" stroke-width="2"><rect x="10" y="14" width="28" height="16"/><circle cx="8" cy="8" r="4"/><circle cx="24" cy="6" r="4"/><circle cx="40" cy="8" r="4"/><path d="M6 38h36"/></svg>
    <div><h3>Lorem ipsum dolor sit amet</h3><p>Lorem ipsum dolor sit amet, consectetur adipiscing elit, sed do eiusmod</p></div>
  </div>
  <div class="t-card" style="top:336px">
    <svg width="48" height="40" viewBox="0 0 48 40" fill="none" stroke="#fff" stroke-width="2"><rect x="4" y="4" width="34" height="24"/><path d="M10 22l8-8 6 5 8-9"/><circle cx="40" cy="30" r="5"/></svg>
    <div><h3>Lorem ipsum dolor sit amet</h3><p>Lorem ipsum dolor sit amet, consectetur adipiscing elit, sed do eiusmod</p></div>
  </div>
  <div class="t-card" style="top:468px">
    <svg width="48" height="40" viewBox="0 0 48 40" fill="none" stroke="#fff" stroke-width="2"><rect x="6" y="6" width="36" height="22"/><path d="M14 36h20M24 28v8M14 20l6-6 5 4 9-8"/></svg>
    <div><h3>Lorem ipsum dolor sit amet</h3><p>Lorem ipsum dolor sit amet, consectetur adipiscing elit, sed do eiusmod</p></div>
  </div>
</section>
<div class="training-photo abs" role="img" aria-label="Nurses in scrubs attending a training session">
  <svg class="play" width="80" height="80" viewBox="0 0 80 80"><circle cx="40" cy="40" r="38" fill="#fff"/><path d="M32 26l22 14-22 14z" fill="#1f1f1f"/></svg>
</div>
<section class="training-note abs">
  <h3>Lorem ipsum dolor sit</h3>
  <div class="rule"></div>
  <p>Lorem ipsum dolor sit amet, consectetur adipiscing elit, sed do eiusmod tempor incididunt ut labore et</p>
</section>

<section class="insights">
  <h2>Latest Insights</h2>
  <div class="rule"></div>
  <article class="post" style="left:112px">
    <div class="post-img" role="img" aria-label="Colleagues in a meeting around a laptop" style="background:linear-gradient(150deg,#e8e8e6,#8a8580 60%,#3b3633)"></div>
    <h3>Lorem ipsum dolor sit amet, consectetur adipiscing elit</h3><a>Learn more</a>
  </article>
  <article class="post" style="left:448px">
    <div class="post-img" role="img" aria-label="Team discussing work at a conference table" style="background:linear-gradient(150deg,#d9dde0,#7b8894 60%,#39424c)"></div>
    <h3>Lorem ipsum dolor sit amet, consectetur adipiscing elit</h3><a>Learn more</a>
  </article>
  <article class="post" style="left:788px">
    <div class="post-img" role="img" aria-label="Nurse caring for an elderly patient" style="background:linear-gradient(150deg,#eef1ef,#7fb3ad 55%,#4a6b6a)"></div>
    <h3>Lorem ipsum dolor sit amet, consectetur adipiscing elit</h3><a>Learn more</a>
  </article>
  <span class="btn view-more abs">View More</span>
</section>

<div class="map abs" role="img" aria-label="Map showing the office location">
  <svg width="40" height="52" viewBox="0 0 40 52"><path d="M20 2C10 2 2 10 2 20c0 14 18 30 18 30s18-16 18-30C38 10 30 2 20 2z" fill="#e2202a"/><circle cx="20" cy="20" r="7" fill="#fff"/></svg>
</div>
<section class="contact abs">
  <div class="dash"></div>
  <h2>Contact us</h2>
  <div class="field" style="top:140px">Name</div>
  <div class="field" style="top:206px">Email</div>
  <div class="field" style="top:272px;height:140px">Message</div>
  <span class="btn">Submit</span>
</section>

<footer class="site-footer abs">
  <div class="foot-brand"><div class="brand-dot"></div><span>Corinne Habbard</span><span style="font-size:13px;font-weight:500">Consulting</span></div>
  <nav class="foot-nav"><span>Home</span><span>About us</span><span>Insights</span><span>Services</span><span>Contact us</span></nav>
  <div class="foot-line"></div>
  <div class="foot-legal"><span>© 2024 Corinne Habbard Consulting. All Rights Reserved.</span><div class="links"><span>Privacy Policy</span><span>Terms Of Services</span><span>Cookies Settings</span></div></div>
</footer>

</body>
</html>
```